PHGCCUL re-branding website and logo

We are looking for a new webpage design and logo our current page address is www.phgccul-example.org. We want to create a new design using PHGCCUL Pinewood and Harbour Growers Co-operative Credit Union limited and another with the purposed new name PHFC Pinewood and Harbour Financial Co-operative, the color scheme is purple and burnt orange. Our new logo and webpage should communicate change and growth purposed theme continuing our legacy here to server past, present and future generations. Our idea for the logo is a live shot of hands of different ages in a circle holding a tree

Target Market(s)

Everyone

Contact Information for Business Card

Company Name
Telephone number
Address
slot to enter employee info

Logo Text

(P & H) Pinewood And Harbour Financial Co-operative

Coding

Coded - Design and coding required

Number of Pages Required

2 page

Colors
f37122
fbed22
6b449b

Requirements
Must have
• links for social media

```html
<!DOCTYPE html>
<html lang="en">
<head>
<meta charset="utf-8">
<title>P &amp; H — Pinewood and Harbour Financial Co-operative</title>
<link href="https://fonts.googleapis.com/css2?family=Mulish:wght@400;600;700&family=Open+Sans:wght@400;600&display=swap" rel="stylesheet">
<style>
:root{
  --orange:#f37122;
  --yellow:#fbed22;
  --purple:#6b449b;
  --black:#000;
  --white:#fff;
  --ink:#2b2b2b;
  --muted:#8a8a8a;
  --grey-band:#ececec;
}
*{box-sizing:border-box;margin:0;padding:0}
html,body{width:1200px;height:2736px;overflow:hidden}
body{position:relative;background:var(--white);font-family:"Open Sans",Arial,sans-serif;color:var(--ink)}
.abs{position:absolute}
h1,h2,h3,h4,.heading{font-family:"Mulish","Helvetica Neue",sans-serif;font-weight:400}
a{color:inherit;text-decoration:none}
.btn{position:absolute;display:flex;align-items:center;justify-content:center;background:var(--orange);color:var(--white);font-size:11px;text-transform:uppercase;letter-spacing:.3px}

/* header */
.site-header{position:absolute;left:0;top:0;width:1200px;height:140px;background:var(--black);color:var(--white)}
.brand{position:absolute;left:137px;top:12px;display:flex;align-items:center;gap:12px}
.brand-mark{width:82px;height:96px;border-radius:50%;background:#5e6b3c}
.brand-name{font-family:"Mulish",sans-serif;font-weight:700;font-size:42px;color:var(--white);letter-spacing:1px}
.header-phone{position:absolute;right:115px;top:24px;font-family:"Mulish",sans-serif;font-size:22px;display:flex;align-items:center;gap:6px}
.main-nav{position:absolute;right:110px;top:80px;display:flex;gap:36px;font-family:"Mulish",sans-serif;font-size:16px;text-transform:uppercase}

/* hero */
.hero{position:absolute;left:0;top:140px;width:1200px;height:491px;background:linear-gradient(180deg,#7fa3c4 0%,#9db4c6 35%,#6c6a63 70%,#4a4538 100%)}
.hero-panel{position:absolute;left:120px;top:134px;width:464px;height:200px;background:rgba(243,113,34,.92);color:var(--white);padding:44px 30px}
.hero-kicker{font-family:"Mulish",sans-serif;font-weight:600;font-size:23px;text-transform:uppercase}
.hero-title{font-family:"Mulish",sans-serif;font-weight:600;font-size:29px;text-transform:uppercase;margin-top:2px}
.hero-text{font-size:14px;line-height:21px;margin-top:8px}
.slider-dots{position:absolute;left:555px;top:466px;display:flex;gap:8px}
.slider-dots span{width:15px;height:15px;border-radius:50%;background:var(--white);border:2px solid #ddd}
.slider-dots span:first-child{background:transparent;border-color:var(--white)}

/* quick actions */
.quick-action{position:absolute;top:666px;width:340px;text-align:center}
.quick-action svg{display:block;margin:0 auto}
.quick-action h3{font-size:24px;margin-top:26px;color:#222}
.quick-action p{font-size:12px;line-height:19px;color:var(--muted);margin-top:6px}
.quick-action .btn{left:115px;top:200px;width:110px;height:31px}

/* promo band */
.promo-band{position:absolute;left:0;top:976px;width:1200px;height:425px;background:var(--purple)}
.promo-card{position:absolute;top:67px;width:485px;height:290px;background:var(--white);overflow:hidden}
.promo-photo{position:absolute;left:0;top:0;width:263px;height:290px}
.promo-body{position:absolute;left:280px;top:58px;width:190px}
.promo-body h3{font-size:26px;line-height:32px;color:#111}
.promo-body p{font-size:12px;line-height:20px;color:var(--muted);margin-top:10px}
.promo-body .btn{position:relative;width:114px;height:31px;margin-top:12px}
.promo-card.is-yellow .yellow-field{position:absolute;top:0;right:0;width:230px;height:290px;background:var(--yellow);clip-path:polygon(40px 0,100% 0,100% 100%,0 100%)}
.promo-card.is-yellow .promo-body p{color:#777}

/* notice */
.notice{position:absolute;left:0;top:1401px;width:1200px;height:469px;background:var(--grey-band)}
.notice-photo{position:absolute;left:600px;top:4px;width:480px;height:465px;background:linear-gradient(180deg,#d9d5d2 0%,#cfc6c0 60%,#e6e3e1 100%)}
.notice h2{position:absolute;left:108px;top:102px;font-size:37px;color:#333}
.notice-sub{position:absolute;left:108px;top:156px;font-family:"Mulish",sans-serif;font-size:20px;line-height:34px;color:#222}
.notice-text{position:absolute;left:108px;top:238px;width:500px;font-size:14px;line-height:25px;color:var(--muted)}
.notice .btn{left:106px;top:308px;width:137px;height:37px;background:var(--purple);font-size:13px}

/* rates & news */
.section-title{position:absolute;top:1946px;font-size:28px;color:#333}
.rate-row{position:absolute;left:113px;width:463px;height:68px;background:var(--yellow);display:flex;align-items:center;padding:0 20px 0 14px}
.rate-row svg{flex:none}
.rate-name{margin-left:14px;font-family:"Mulish",sans-serif;font-size:17px;color:#222;line-height:19px}
.rate-name small{display:block;font-size:12px;color:#555}
.rate-value{margin-left:auto;font-size:17px;color:#333;align-self:flex-start;margin-top:16px}
.news-item{position:absolute;left:622px;width:480px}
.news-photo{position:absolute;left:0;top:0;width:128px;height:128px;border-radius:50%}
.news-item h4{position:absolute;left:150px;top:14px;font-size:20px;color:#222}
.news-item p{position:absolute;left:150px;top:44px;width:330px;font-size:12px;line-height:20px;color:var(--muted)}
.news-item .read-more{position:absolute;left:150px;top:114px;font-size:12px;color:var(--orange);text-transform:uppercase}

/* footer */
.site-footer{position:absolute;left:0;top:2371px;width:1200px;height:365px;background:var(--black);color:var(--white)}
.footer-col{position:absolute;top:62px}
.footer-col h4{font-family:"Mulish",sans-serif;font-size:17px;text-transform:uppercase;margin-bottom:12px}
.footer-col li{list-style:none;font-size:13px;line-height:28.6px}
.social-links{position:absolute;left:515px;top:210px;display:flex;gap:12px}
.social-links a{width:36px;height:36px;border-radius:50%;background:var(--purple)}
.footer-brand{position:absolute;left:784px;top:42px;display:flex;align-items:center;gap:12px}
.footer-brand .brand-mark{width:78px;height:96px}
.footer-rule{position:absolute;left:91px;top:287px;width:985px;height:1px;background:#333}
.copyright{position:absolute;left:0;top:319px;width:1200px;text-align:center;font-size:13px;color:#aaa}
</style>
</head>
<body>

<header class="site-header">
  <div class="brand">
    <div class="brand-mark" role="img" aria-label="Circular logo photo area"></div>
    <span class="brand-name">P &amp; H</span>
  </div>
  <div class="header-phone">
    <svg width="20" height="20" viewBox="0 0 24 24"><path fill="#f5c242" d="M6.6 10.8a15.1 15.1 0 0 0 6.6 6.6l2.2-2.2a1 1 0 0 1 1-.25 11.4 11.4 0 0 0 3.6.57 1 1 0 0 1 1 1V20a1 1 0 0 1-1 1A17 17 0 0 1 3 4a1 1 0 0 1 1-1h3.5a1 1 0 0 1 1 1c0 1.25.2 2.45.57 3.57a1 1 0 0 1-.25 1z"/></svg>
    (555) 014-3872
  </div>
  <nav class="main-nav">
    <a href="#">Apply Loan</a>
    <a href="#">Product &amp; Services</a>
    <a href="#">Tools &amp; Benefits</a>
    <a href="#">My Credit Union</a>
  </nav>
</header>

<section class="hero" role="img" aria-label="City skyline photograph with office towers under a blue sky">
  <div class="hero-panel">
    <div class="hero-kicker">Curabitur vel misit amet</div>
    <div class="hero-title">Magna malesuada ultric</div>
    <p class="hero-text">interdum vel blandit sed nulla in ullamcorper est<br>eget tempor cursus neque mi consec</p>
  </div>
  <div class="slider-dots"><span></span><span></span><span></span><span></span></div>
</section>

<section class="quick-actions">
  <div class="quick-action" style="left:104px">
    <svg width="110" height="90" viewBox="0 0 110 90" fill="none" stroke="#6b449b" stroke-width="3">
      <circle cx="55" cy="12" r="7"/><path d="M44 42v-12a11 11 0 0 1 22 0v12z"/>
      <circle cx="20" cy="55" r="7"/><path d="M9 85v-12a11 11 0 0 1 22 0v12z"/>
      <circle cx="90" cy="55" r="7"/><path d="M79 85v-12a11 11 0 0 1 22 0v12z"/>
      <path d="M55 42v14M55 56L35 68M55 56L75 68"/>
    </svg>
    <h3>Apply for Loan</h3>
    <p>Morbi diam mauris viverra in gravida eu mattis<br>in ante Morbi eget arcu</p>
    <a class="btn" href="#">Click here</a>
  </div>
  <div class="quick-action" style="left:437px">
    <svg width="110" height="90" viewBox="0 0 110 90" fill="none" stroke="#6b449b" stroke-width="3">
      <circle cx="58" cy="36" r="13"/><circle cx="78" cy="16" r="10"/>
      <path d="M10 62h22l14 8h22a5 5 0 0 1 0 10H44"/><path d="M68 76l26-14a6 6 0 0 1 6 10L72 88H10"/>
      <path d="M58 29v14M54 32h6M56 40h6"/>
    </svg>
    <h3>Become a Member</h3>
    <p>Morbi diam mauris viverra in gravida eu mattis<br>in ante Morbi eget arcu</p>
    <a class="btn" href="#">Click here</a>
  </div>
  <div class="quick-action" style="left:773px">
    <svg width="110" height="90" viewBox="0 0 110 90" fill="none" stroke="#6b449b" stroke-width="3">
      <rect x="30" y="2" width="52" height="86" rx="6"/><rect x="39" y="12" width="34" height="20"/>
      <g fill="#6b449b" stroke="none">
        <rect x="39" y="42" width="8" height="7"/><rect x="52" y="42" width="8" height="7"/><rect x="65" y="42" width="8" height="7"/>
        <rect x="39" y="55" width="8" height="7"/><rect x="52" y="55" width="8" height="7"/><rect x="65" y="55" width="8" height="7"/>
        <rect x="39" y="68" width="8" height="7"/><rect x="52" y="68" width="8" height="7"/><rect x="65" y="68" width="8" height="7"/>
      </g>
    </svg>
    <h3>Financial Calculators</h3>
    <p>Morbi diam mauris viverra in gravida eu mattis<br>in ante Morbi eget arcu</p>
    <a class="btn" href="#">Click here</a>
  </div>
</section>

<section class="promo-band">
  <article class="promo-card" style="left:111px">
    <div class="promo-photo" role="img" aria-label="Photo of a smiling member reading a letter at a desk" style="background:linear-gradient(135deg,#c9b9a6,#8d7563 60%,#5e6f86)"></div>
    <div class="promo-body">
      <h3>My Credit<br>Union</h3>
      <p>interdum vel blandit sed nulla in ullamcorper est eget tempor cursus neque mi cons</p>
      <a class="btn" href="#">Click here</a>
    </div>
  </article>
  <article class="promo-card is-yellow" style="left:607px">
    <div class="promo-photo" role="img" aria-label="Photo of a cheerful member giving a thumbs up at a laptop" style="width:300px;background:linear-gradient(135deg,#e9e6e2,#c8a594 55%,#d2523a)"></div>
    <div class="yellow-field"></div>
    <div class="promo-body">
      <h3>Product &amp;<br>Services</h3>
      <p>interdum vel blandit sed nulla in ullamcorper est eget tempor cursus neque mi cons</p>
      <a class="btn" href="#">Click here</a>
    </div>
  </article>
</section>

<section class="notice">
  <div class="notice-photo" role="img" aria-label="Photo of a smiling member holding up a bank card"></div>
  <h2>ATM Card Renewal Notice</h2>
  <div class="notice-sub">Please b adviced that all ATM Cards issues Feb 2014<br>EXPIRES EFFECTIVE FEB 28, 2017</div>
  <p class="notice-text">Curabitur vel mi sit amet magna malesuada ultrices Ut nisi erat fermentum vel congue id euismod in elit Fusce</p>
  <a class="btn" href="#">Click here</a>
</section>

<section class="rates">
  <h2 class="section-title" style="left:114px">Featured Rates</h2>
  <div class="rate-row" style="top:2003px">
    <svg width="46" height="40" viewBox="0 0 46 40" fill="none" stroke="#222" stroke-width="2.2"><circle cx="23" cy="12" r="8"/><path d="M8 38c0-9 7-15 15-15s15 6 15 15z"/></svg>
    <div class="rate-name">Consumer Loans<small>as low as</small></div>
    <div class="rate-value">9.00% ARP</div>
  </div>
  <div class="rate-row" style="top:2080px">
    <svg width="62" height="40" viewBox="0 0 62 40" fill="none" stroke="#111" stroke-width="3"><circle cx="12" cy="27" r="9"/><circle cx="50" cy="27" r="9"/><path d="M12 27l12-12h14l12 12M24 15l4-6h8M32 27h10"/></svg>
    <div class="rate-name">New Auto/Motorcycle<small>as low as</small></div>
    <div class="rate-value">7.00% ARP</div>
  </div>
  <div class="rate-row" style="top:2156px">
    <svg width="46" height="40" viewBox="0 0 46 40" fill="none" stroke="#222" stroke-width="2.2"><circle cx="10" cy="30" r="7"/><circle cx="36" cy="30" r="7"/><path d="M10 30h14l6-14h8M30 16l-4-8h-6"/></svg>
    <div class="rate-name">Used Auto/Motorcycle<small>as low as</small></div>
    <div class="rate-value">11.75% ARP</div>
  </div>
  <div class="rate-row" style="top:2233px">
    <svg width="46" height="40" viewBox="0 0 46 40" fill="none" stroke="#222" stroke-width="2.2"><path d="M4 20L23 4l19 16M9 16v21h28V16"/><path d="M18 30l10-10"/><circle cx="19" cy="21" r="2"/><circle cx="27" cy="29" r="2"/></svg>
    <div class="rate-name">Mortgages<small>as low as</small></div>
    <div class="rate-value">8.25% ARP</div>
  </div>
</section>

<section class="news">
  <h2 class="section-title" style="left:626px">News &amp; Events</h2>
  <article class="news-item" style="top:2001px">
    <div class="news-photo" role="img" aria-label="Photo of a handshake at a business meeting" style="background:radial-gradient(circle at 40% 40%,#8aa3c0,#1d2a44 75%)"></div>
    <h4>Morbi diam mauris viverra</h4>
    <p>in gravida eu mattis in ante Morbi eget arcu Morbi porta libero id ullamcorper nonummy nibh ligula pulvinar metus eget</p>
    <a class="read-more" href="#">Read more</a>
  </article>
  <article class="news-item" style="top:2165px">
    <div class="news-photo" role="img" aria-label="Photo of colleagues talking at an office event" style="background:radial-gradient(circle at 50% 40%,#d8d2c8,#6e6a62 75%)"></div>
    <h4>Donec convallis pede</h4>
    <p>in gravida eu mattis in ante Morbi eget arcu Morbi porta libero id ullamcorper nonummy nibh ligula pulvinar metus eget</p>
    <a class="read-more" href="#">Read more</a>
  </article>
</section>

<footer class="site-footer">
  <div class="footer-col" style="left:106px">
    <h4>Quick Links</h4>
    <ul><li>Home</li><li>Apply Now</li><li>My Credit Union</li><li>Product &amp; Services</li></ul>
  </div>
  <div class="footer-col" style="left:303px">
    <h4>Resources</h4>
    <ul><li>Apply for Loan</li><li>Tools &amp; Benefits</li><li>Resources</li><li>Contact Us</li></ul>
  </div>
  <div class="footer-col" style="left:518px">
    <h4>Contact Info</h4>
    <ul><li>The Cedar Lane Commons</li><li>2210 Orchard Avenue</li><li>Millbrook, Colorado 80999</li><li>P:(555) 014-3872</li></ul>
  </div>
  <nav class="social-links">
    <a href="#" aria-label="Social network link"></a>
    <a href="#" aria-label="Social network link"></a>
    <a href="#" aria-label="Social network link"></a>
    <a href="#" aria-label="Social network link"></a>
  </nav>
  <div class="footer-brand">
    <div class="brand-mark" role="img" aria-label="Circular logo photo area"></div>
    <span class="brand-name">P &amp; H</span>
  </div>
  <div class="footer-rule"></div>
  <p class="copyright">© 2017 Company Name &nbsp;All right reserved &nbsp;Term of Use</p>
</footer>

</body>
</html>
```